Upstart Retirement Planning Firm needs help with business card design

Harborview Nest Advisors, LLC is looking for help with business card design. We give advice on investments, insurance, and other financial matters related to retirement. There are some required disclosures that we will provide but mostly we are looking for a professional, classy business card that reflects the theme we have chosen. We have a logo that is attached but we would like to add a phrase; "Turning Your Earned Income Into Retirement Income"

Doubled sided only so that we can add the required disclosures (needed for our industry) on the back of the card. We will provide the exact words for this in 1-2 days.

Target Market(s)

Retirees and Pre-retirees. Professionals 50+ years old

Industry/Entity Type

Financial Planning

Contact Information for Business Card

We currently have two people who will need separate cards so we'd like to have a template so that we can add names for new cards in the future.

For the first run, please show the following information.

Gregor Pelham, MBA, ChFC®, CLU®
Financial Advisor, Registered Representative
gpelham@harborviewnest.example
Phone: (555) 318-2946
Toll Free Fax: (800) 555-0193

Address is
2187 Meadowlark Ridge Rd.
Suite K418
Virginia Beach, VA 23999

Colors
3277b5

Requirements
Must have
• Logo, contact info, small phase to describe business (in description), required legal disclosures on back of the card as follows (in small font)
• Gregor Pelham is a registered representative of and offers securities through Brightmoor Capital Brokerage Corporation, Member FNQX. Brightmoor Capital Brokerage Corporation is a member of the Brightmoor Capital Alliance which is the marketing name for Brightmoor Holding Corporation and its affiliates.
Nice to have
• Rounded edges, raised letters
Should not have
• any colors that aren't in the logo (other than black for font)

```html
<!DOCTYPE html>
<html lang="en">
<head>
<meta charset="utf-8">
<title>Harborview Nest Advisors – Business Card</title>
<link rel="stylesheet" href="https://fonts.googleapis.com/css2?family=Source+Sans+3:wght@400&display=swap">
<style>
  :root {
    --brand-blue: #2b579a;
    --brand-grey: #c9c9c9;
    --ink: #111418;
    --paper: #ffffff;
    --backdrop: #e4e4e4;
  }
  * { box-sizing: border-box; margin: 0; padding: 0; }
  html, body { width: 1189px; height: 1200px; overflow: hidden; }
  body {
    position: relative;
    background: var(--backdrop);
    font-family: "Source Sans 3", "Myriad Pro", sans-serif;
    color: var(--ink);
  }
  .card { position: absolute; left: 140px; width: 917px; height: 524px; background: var(--paper); }
  .card--front { top: 45px; }
  .card--back {
    top: 624px;
    padding: 11px;
    background: linear-gradient(to bottom, var(--brand-blue) 0%, var(--brand-blue) 45%, #a7abb1 100%);
  }
  .card__inner { width: 100%; height: 100%; background: var(--paper); position: relative; }

  .brand-name {
    position: absolute; left: 0; right: 0; text-align: center;
    color: var(--brand-blue); font-weight: 400; white-space: nowrap;
  }
  .card--front .brand-name { top: 110px; font-size: 40px; }
  .card--back .brand-name { top: 220px; font-size: 52px; }

  .grey-band { position: absolute; left: 0; top: 263px; width: 100%; height: 21px; background: var(--brand-grey); }
  .info-panel { position: absolute; left: 0; top: 284px; width: 100%; height: 240px; background: var(--brand-blue); }

  .identity { position: absolute; left: 54px; top: 30px; }
  .identity__name { font-size: 43px; line-height: 1.1; }
  .identity__detail { font-size: 22px; line-height: 33px; }

  .panel-divider { position: absolute; left: 377px; top: 24px; width: 2px; height: 184px; background: var(--ink); }

  .contact-list { position: absolute; left: 410px; top: 44px; list-style: none; font-size: 23.5px; line-height: 34px; }
  .contact-list li { display: flex; align-items: flex-start; }
  .contact-list li + li { margin-top: 0; }
  .contact-list .addr { margin-top: 3px; }
  .contact-icon { width: 19px; height: 19px; margin: 8px 16px 0 0; flex: none; }
</style>
</head>
<body>
  <section class="card card--front">
    <p class="brand-name">Harborview Nest Advisors, LLC</p>
    <div class="grey-band"></div>
    <div class="info-panel">
      <div class="identity">
        <h1 class="identity__name" style="font-weight:400">Gregor Pelham</h1>
        <p class="identity__detail">MBA, ChFC®, CLU®</p>
        <p class="identity__detail">Financial Advisor,</p>
        <p class="identity__detail">Registered Representative</p>
      </div>
      <div class="panel-divider"></div>
      <ul class="contact-list">
        <li>
          <svg class="contact-icon" viewBox="0 0 20 20" aria-hidden="true"><rect width="20" height="20" fill="#111418"/><path d="M6 4h3l1 4-2 1a7 7 0 0 0 3 3l1-2 4 1v3c-6 1-11-4-10-10z" fill="#2b579a"/></svg>
          <span>(555) 318-2946</span>
        </li>
        <li>
          <svg class="contact-icon" viewBox="0 0 20 20" aria-hidden="true"><rect width="20" height="20" fill="#111418"/><rect x="4" y="8" width="12" height="7" fill="#2b579a"/><rect x="6" y="4" width="8" height="4" fill="#2b579a"/></svg>
          <span>(800) 555-0193</span>
        </li>
        <li>
          <svg class="contact-icon" viewBox="0 0 20 20" aria-hidden="true"><rect width="20" height="20" fill="#111418"/><rect x="4" y="6" width="12" height="8" fill="none" stroke="#2b579a" stroke-width="1.5"/><path d="M4 6l6 5 6-5" fill="none" stroke="#2b579a" stroke-width="1.5"/></svg>
          <span>gpelham@harborviewnest.example</span>
        </li>
        <li class="addr">
          <svg class="contact-icon" viewBox="0 0 20 20" aria-hidden="true"><rect width="20" height="20" fill="#111418"/><path d="M10 4l6 6h-2v5H6v-5H4z" fill="#2b579a"/></svg>
          <span>2187 Meadowlark Ridge Rd. Suite K418<br>Virginia Beach, VA 23999</span>
        </li>
      </ul>
    </div>
  </section>

  <section class="card card--back">
    <div class="card__inner">
      <p class="brand-name">Harborview Nest Advisors, LLC</p>
    </div>
  </section>
</body>
</html>
```